Meridale Real Estate

We are looking for help with web design for a new company that is revolutionizing the real estate world on the listing side: by charing per hour for top level professional real estate services. We would like the concept to be simple, clean and easily understood.
Updates

We want this website to actually function, not just a static design.

Industry/Entity Type

Real Estate

```html
<!DOCTYPE html>
<html lang="en">
<head>
<meta charset="utf-8">
<title>Meridale Real Estate</title>
<link rel="stylesheet" href="https://fonts.googleapis.com/css2?family=Arimo:wght@400;700&family=Mulish:wght@700;800&display=swap">
<style>
:root{
  --page:#eeeeee;
  --header:#f4f4f4;
  --ink:#222222;
  --text:#444444;
  --muted:#666666;
  --accent:#7cc0e4;
  --dark:#2e2e2e;
  --footer:#333333;
  --teal:#17aac0;
  --green:#2e9a3c;
  --dot:#9a9a9a;
  --star:#e8321c;
  --star-off:#b8b8b8;
  --field:#ffffff;
  --field-line:#c9c9c9;
}
*{box-sizing:border-box;margin:0;padding:0}
html,body{width:972px;height:1200px;overflow:hidden}
body{position:relative;background:var(--page);font-family:"Arimo",Arial,sans-serif;color:var(--text)}
.abs{position:absolute}

/* header */
.site-header{left:0;top:0;width:972px;height:114px;background:var(--header)}
.brand{left:108px;top:42px;display:flex;align-items:center;gap:8px}
.brand-mark{width:16px;height:16px;border:2px solid var(--ink);border-radius:50%}
.brand-name{font-family:"Mulish",sans-serif;font-weight:800;font-size:17px;color:var(--ink);letter-spacing:.5px}
.account-tab{left:696px;top:0;width:161px;height:29px;background:var(--dark);border-radius:0 0 10px 10px;display:flex;align-items:center;justify-content:center;gap:14px;color:#fff;font-size:11px}
.account-tab span{display:flex;align-items:center;gap:6px}
.account-tab .sep{width:1px;height:18px;background:#666}
.main-nav{left:396px;top:68px;width:462px;display:flex;justify-content:space-between;padding:0 18px 0 20px;font-size:13px;color:var(--ink)}
.nav-line{left:396px;top:88px;width:462px;height:3px;background:var(--accent)}
.nav-dot{left:425px;top:86px;width:8px;height:8px;border-radius:50%;background:#555;border:2px solid #ddd}

/* hero */
.hero{left:0;top:114px;width:972px;height:366px;background:linear-gradient(180deg,#a8bccb 0%,#9fb3c3 55%,#7f8f88 78%,#6d7a4e 100%)}
.hero-arrow{top:266px;width:38px;height:38px;border-radius:50%;background:#fff;display:flex;align-items:center;justify-content:center}
.search-band{left:0;top:426px;width:972px;height:54px;background:rgba(110,128,60,.85)}
.field{height:25px;background:var(--field);border:1px solid var(--field-line);font-size:11px;color:#333;display:flex;align-items:center;justify-content:space-between;padding:0 7px}
.search-btn{left:722px;top:443px;width:92px;height:25px;background:var(--teal);color:#fff;font-weight:700;font-size:12px;display:flex;align-items:center;justify-content:center}

/* listing */
.photo-frame{left:112px;top:511px;width:379px;height:167px;background:#fff;border:1px solid #d6d6d6;padding:6px}
.photo{width:100%;height:100%;background:linear-gradient(160deg,#9cc3e6 0%,#c9d8e4 40%,#c47a4c 65%,#6f8a4a 100%)}
.thumb{top:688px;width:76px;height:66px;background:#fff;border:1px solid #d6d6d6;padding:3px}
.thumb div{width:100%;height:100%}
.thumb-arrow{top:712px}
.listing-title{left:516px;top:513px;font-family:"Mulish",sans-serif;font-weight:800;font-size:15px;color:var(--ink)}
.listing-text{left:516px;top:541px;width:340px;font-size:10.4px;line-height:16px;color:var(--text)}
.facts{left:516px;font-size:10.5px;color:#333;display:flex;gap:22px;align-items:center}
.facts b{font-weight:700;color:var(--ink)}

/* sections */
.section-title{font-family:"Mulish",sans-serif;font-weight:800;font-size:15px;color:var(--ink)}
.map{left:112px;top:800px;width:379px;height:167px;border:1px solid #d6d6d6;background:linear-gradient(135deg,#e9e4d6 0%,#f1ead0 45%,#dfe6cf 70%,#e8e2d2 100%)}
.amenities{left:516px;top:799px;width:360px;display:grid;grid-template-columns:116px 118px 120px;font-size:10.3px;color:#444}
.amenities ul{list-style:none}
.amenities li{height:21.3px;display:flex;align-items:center;gap:9px}
.bullet{width:11px;display:flex;justify-content:center}
.bullet i{width:6px;height:6px;border-radius:50%;background:var(--dot)}

/* contact */
.contact-field{top:1020px;width:150px;height:22px;background:var(--field);border:1px solid var(--field-line);font-size:11px;color:#333;padding:0 7px;display:flex;align-items:center}
.send-btn{left:784px;top:1019px;width:67px;height:25px;border:1px solid #bdbdbd;border-radius:3px;background:linear-gradient(#fafafa,#dcdcdc);font-size:11px;font-weight:700;color:#333;display:flex;align-items:center;justify-content:center}

/* footer */
.site-footer{left:0;top:1090px;width:972px;height:110px;background:var(--footer);color:#fff;text-align:center}
.footer-nav{position:absolute;top:18px;width:100%;font-size:10.5px}
.footer-nav span{margin:0 8px}
.copyright{position:absolute;top:45px;width:100%;font-size:10px;font-weight:700}
.social{position:absolute;top:69px;left:432px;display:flex;gap:17px}
.social i{width:23px;height:23px;border-radius:50%;background:#9a9a9a;display:block}
</style>
</head>
<body>

<header class="abs site-header"></header>
<div class="abs brand"><span class="brand-mark"></span><span class="brand-name">Meridale Real Estate</span></div>
<div class="abs account-tab">
  <span><svg width="13" height="13" viewBox="0 0 13 13"><rect x="5" y="1" width="7" height="11" fill="none" stroke="#fff" stroke-width="1.4"/><path d="M1 6.5h6M5 4l2.5 2.5L5 9" fill="none" stroke="#fff" stroke-width="1.4"/></svg>Login</span>
  <span class="sep"></span>
  <span><svg width="13" height="13" viewBox="0 0 13 13"><rect x="1" y="2" width="9" height="10" fill="none" stroke="#fff" stroke-width="1.4"/><path d="M5 8l7-7" stroke="#fff" stroke-width="1.8"/></svg>Register</span>
</div>
<nav class="abs main-nav"><span>Home</span><span>About Us</span><span>Features</span><span>Properties</span><span>Contact Us</span></nav>
<div class="abs nav-line"></div>
<div class="abs nav-dot"></div>

<section class="abs hero" role="img" aria-label="Living room interior with blue sofa, framed pictures and bookshelves"></section>
<div class="abs hero-arrow" style="left:31px"><svg width="12" height="14" viewBox="0 0 12 14"><path d="M9 1L3 7l6 6" fill="none" stroke="#444" stroke-width="3"/></svg></div>
<div class="abs hero-arrow" style="left:903px"><svg width="12" height="14" viewBox="0 0 12 14"><path d="M3 1l6 6-6 6" fill="none" stroke="#444" stroke-width="3"/></svg></div>
<div class="abs search-band"></div>
<div class="abs field" style="left:158px;top:443px;width:186px">Location</div>
<div class="abs field" style="left:356px;top:443px;width:113px">Check in<svg width="14" height="13" viewBox="0 0 14 13"><rect x="1" y="2" width="12" height="10" fill="none" stroke="#333"/><rect x="1" y="2" width="12" height="3" fill="#333"/><path d="M4 7h1M7 7h1M10 7h1M4 10h1M7 10h1M10 10h1" stroke="#333"/></svg></div>
<div class="abs field" style="left:481px;top:443px;width:113px">Check out<svg width="14" height="13" viewBox="0 0 14 13"><rect x="1" y="2" width="12" height="10" fill="none" stroke="#333"/><rect x="1" y="2" width="12" height="3" fill="#333"/><path d="M4 7h1M7 7h1M10 7h1M4 10h1M7 10h1M10 10h1" stroke="#333"/></svg></div>
<div class="abs field" style="left:606px;top:443px;width:104px">2 Guest<svg width="14" height="9" viewBox="0 0 14 9"><path d="M0 0h14L7 9z" fill="#111"/></svg></div>
<div class="abs search-btn">SEARCH</div>

<div class="abs photo-frame"><div class="photo" role="img" aria-label="Modern apartment building with balconies"></div></div>
<svg class="abs thumb-arrow" style="left:111px" width="9" height="16" viewBox="0 0 9 16"><path d="M8 1L1 8l7 7" fill="none" stroke="#888" stroke-width="1.5"/></svg>
<div class="abs thumb" style="left:128px"><div role="img" aria-label="Apartment building exterior" style="background:linear-gradient(160deg,#9cc3e6,#c47a4c 60%,#6f8a4a)"></div></div>
<div class="abs thumb" style="left:218px"><div role="img" aria-label="Bright white kitchen" style="background:linear-gradient(160deg,#f2f2f2,#d8dadb)"></div></div>
<div class="abs thumb" style="left:308px"><div role="img" aria-label="White living room" style="background:linear-gradient(160deg,#e4e4e2,#c8c8c4)"></div></div>
<div class="abs thumb" style="left:397px"><div role="img" aria-label="House with swimming pool" style="background:linear-gradient(160deg,#9fbcd2,#d8d2c2 60%,#7eb0c8)"></div></div>
<svg class="abs thumb-arrow" style="left:481px" width="9" height="16" viewBox="0 0 9 16"><path d="M1 1l7 7-7 7" fill="none" stroke="#888" stroke-width="1.5"/></svg>

<h1 class="abs listing-title">Ut us dolor apibusgetele mentumvel</h1>
<p class="abs listing-text">Vestibulum feugiat tempor mattis. Maecenas venenatis at erat sit amet viverra. Fusce sagittis pretium est vel iaculis. Proin vel tincidunt nisi. Sed non vehicula purus. In auctor sodales metus, ac fermentum odio sagittis quis. Curabitur volutpat, erat nec varius dapibus, felis libero malesuada mauris, at vestibulum enim erat non nibh. Donec ac nibh dapibus.</p>
<div class="abs facts" style="top:631px"><span><b>Price</b> &nbsp;: &nbsp;$3000</span><span><b>Baths</b> &nbsp;: &nbsp;2</span><span><b>Beds</b> &nbsp;: &nbsp;4</span></div>
<div class="abs facts" style="top:656px"><span><b>Garages</b> &nbsp;: &nbsp;2</span><span><b>Area</b> &nbsp;: &nbsp;234</span></div>
<div class="abs facts" style="top:683px"><span style="display:flex;align-items:center;gap:10px"><b>Check Property Available / Not Available</b><svg width="15" height="14" viewBox="0 0 14 13"><rect x="1" y="2" width="12" height="10" fill="none" stroke="#333"/><rect x="1" y="2" width="12" height="3" fill="#333"/><path d="M4 7h1M7 7h1M10 7h1M4 10h1M7 10h1M10 10h1" stroke="#333"/></svg></span></div>
<div class="abs facts" style="top:710px;gap:14px"><b>Rating &nbsp;:</b>
  <svg width="106" height="17" viewBox="0 0 106 17">
    <defs><path id="star" d="M8 0l2.4 5.3 5.6.6-4.2 3.8 1.2 5.6L8 12.4 3 15.3l1.2-5.6L0 5.9l5.6-.6z"/></defs>
    <use href="#star" x="0" fill="#e8321c"/><use href="#star" x="22" fill="#e8321c"/><use href="#star" x="44" fill="#e8321c"/><use href="#star" x="66" fill="#b8b8b8"/><use href="#star" x="88" fill="#b8b8b8"/>
  </svg>
</div>

<h2 class="abs section-title" style="left:112px;top:774px">Property Location Map</h2>
<div class="abs map" role="img" aria-label="Street map showing the property location"></div>

<h2 class="abs section-title" style="left:516px;top:774px">Amenities</h2>
<svg width="0" height="0" style="position:absolute"><defs><path id="tick" d="M1 6l3.5 3.5L11 2" fill="none" stroke="#2e9a3c" stroke-width="2"/></defs></svg>
<div class="abs amenities">
  <ul>
    <li><span class="bullet"><svg width="12" height="11"><use href="#tick"/></svg></span>Air Conditioning</li>
    <li><span class="bullet"><svg width="12" height="11"><use href="#tick"/></svg></span>Cable TV</li>
    <li><span class="bullet"><i></i></span>Computer</li>
    <li><span class="bullet"><i></i></span>DVD</li>
    <li><span class="bullet"><svg width="12" height="11"><use href="#tick"/></svg></span>Juicer</li>
    <li><span class="bullet"><i></i></span>Oven</li>
    <li><span class="bullet"><svg width="12" height="11"><use href="#tick"/></svg></span>Radio</li>
    <li><span class="bullet"><svg width="12" height="11"><use href="#tick"/></svg></span>Use of pool</li>
  </ul>
  <ul>
    <li><span class="bullet"><i></i></span>Balcony</li>
    <li><span class="bullet"><svg width="12" height="11"><use href="#tick"/></svg></span>Cleaning after exit</li>
    <li><span class="bullet"><svg width="12" height="11"><use href="#tick"/></svg></span>Cot</li>
    <li><span class="bullet"><i></i></span>Fan</li>
    <li><span class="bullet"><svg width="12" height="11"><use href="#tick"/></svg></span>Hairdryer</li>
    <li><span class="bullet"><i></i></span>Internet</li>
    <li><span class="bullet"><svg width="12" height="11"><use href="#tick"/></svg></span>Lift</li>
    <li><span class="bullet"><svg width="12" height="11"><use href="#tick"/></svg></span>Toaster</li>
  </ul>
  <ul style="margin-top:-3px">
    <li><span class="bullet"><svg width="12" height="11"><use href="#tick"/></svg></span>Dishwasher</li>
    <li><span class="bullet"><i></i></span>Fridge</li>
    <li><span class="bullet"><svg width="12" height="11"><use href="#tick"/></svg></span>Heating</li>
    <li><span class="bullet"><i></i></span>Microwave</li>
    <li><span class="bullet"><i></i></span>Smoking allowed</li>
    <li><span class="bullet"><i></i></span>Towelwes</li>
    <li><span class="bullet"><svg width="12" height="11"><use href="#tick"/></svg></span>Iron</li>
    <li><span class="bullet"><svg width="12" height="11"><use href="#tick"/></svg></span>Roof terrace</li>
  </ul>
</div>

<h2 class="abs section-title" style="left:112px;top:987px">Contact Form</h2>
<div class="abs contact-field" style="left:112px">Name</div>
<div class="abs contact-field" style="left:278px">Email</div>
<div class="abs contact-field" style="left:445px">Phone</div>
<div class="abs contact-field" style="left:612px">Message</div>
<div class="abs send-btn">SEND</div>

<footer class="abs site-footer">
  <nav class="footer-nav"><span>Home</span>|<span>About Us</span>|<span>Features</span>|<span>Properties</span>|<span>Contact Us</span></nav>
  <p class="copyright">© Copyrights 2015 Meridale Real Estate. All Right Reserved</p>
  <div class="social"><i></i><i></i><i></i></div>
</footer>

</body>
</html>
```